Business card design Needed for new logo / Construction business, home extensions and new builds

We need a business card design using our new logo files which i will attach to this project :)

We are a small construction business specialising in home extensions, new builds and property development. We are very ambitious and would appreciate professional and elegant designs for our new business card.

Very serious about using the services on MakerQuarry and recently acquired our new logo from here :)

Please get involved, i will feedback when i can as i am very busy but can respond daily, thanks

Target Market(s)

People that want to build onto their houses, new building developments or adding too their existing property

Industry/Entity Type

Construction

Contact Information for Business Card

Renwick Tolliver Construction, Lionel Ashby (Managing Director), Tel 07822254961, email - info@renwick-tolliver, www.renwick-tolliver.co.uk

Colors

Designer to choose colors to be used in the design.

Requirements
Must have
• I like a deep grey on the back please. A lot of you have provided black from and back, try mixing things up a little. The black looks cool 😎 Thanks

```html
<!DOCTYPE html>
<html lang="en">
<head>
<meta charset="utf-8">
<title>Renwick Tolliver Construction — Business Card</title>
<link rel="stylesheet" href="https://fonts.googleapis.com/css2?family=Cinzel:wght@400;600&family=Montserrat:wght@400;500&display=swap">
<style>
  :root {
    --stage: #1c1c1c;
    --card-grey: #666666;
    --card-grey-deep: #5c5c5c;
    --pattern-dark: #3e3e3e;
    --pattern-light: #8a8a8a;
    --gold: #d6a43a;
    --edge-gold: #c8922c;
    --silver: #e6e6e6;
    --white: #f4f4f4;
  }
  * { box-sizing: border-box; margin: 0; padding: 0; }
  html, body {
    width: 1200px; height: 987px; overflow: hidden;
    background: var(--stage);
  }
  .canvas {
    position: relative; width: 1200px; height: 987px;
    display: flex; flex-direction: column; align-items: center; justify-content: center; gap: 48px;
  }
  .card {
    position: relative; width: 700px; height: 400px;
    border-radius: 22px;
    background: var(--card-grey);
    border-bottom: 4px solid var(--edge-gold);
    box-shadow: 0 3px 0 var(--edge-gold);
    overflow: hidden;
  }
  /* Back side */
  .card--back { background: var(--card-grey-deep); }
  .back-pattern {
    position: absolute; inset: 0;
    background: linear-gradient(200deg, var(--pattern-light) 0%, var(--card-grey-deep) 45%, var(--pattern-dark) 100%);
    opacity: 0.55;
  }
  .back-mark {
    position: absolute; right: 70px; top: 150px;
    display: flex; align-items: center; gap: 8px;
    font-family: "Cinzel", serif; font-weight: 600; font-size: 18px;
    color: var(--gold); letter-spacing: 1px;
  }
  .mark-square { width: 12px; height: 12px; background: var(--gold); }

  /* Front side */
  .company {
    position: absolute; left: 50px; top: 66px; text-align: center; width: 330px;
  }
  .company__name {
    font-family: "Cinzel", serif; font-weight: 400; font-size: 31px;
    color: var(--silver); letter-spacing: 1px; white-space: nowrap;
  }
  .company__trade {
    display: flex; align-items: center; justify-content: center; gap: 12px;
    font-family: "Cinzel", serif; font-size: 20px; color: var(--gold);
    letter-spacing: 2px; margin-top: 2px;
  }
  .company__trade::before, .company__trade::after {
    content: ""; width: 44px; height: 2px;
    background: linear-gradient(90deg, transparent, var(--gold));
  }
  .company__trade::after { transform: scaleX(-1); }

  .person { position: absolute; left: 120px; top: 196px; }
  .person__name {
    font-family: "Cinzel", serif; font-size: 29px; color: var(--gold); letter-spacing: 1px;
  }
  .person__role {
    font-family: "Montserrat", sans-serif; font-size: 17px; color: var(--white); margin-top: 2px;
  }

  .contacts {
    position: absolute; left: 120px; top: 290px; list-style: none;
    font-family: "Montserrat", sans-serif; font-size: 17px; color: var(--white);
  }
  .contacts li { display: flex; align-items: center; gap: 10px; line-height: 30px; }
  .contacts svg { width: 14px; height: 14px; flex: none; }

  .front-mark {
    position: absolute; right: 54px; top: 44px; width: 250px; height: 210px;
    display: flex; flex-direction: column; align-items: center; justify-content: center; gap: 12px;
    font-family: "Cinzel", serif; font-weight: 600; font-size: 44px; line-height: 1.05;
    color: var(--gold); letter-spacing: 1px; text-align: center;
  }
  .front-mark .mark-square { width: 26px; height: 26px; }
</style>
</head>
<body>
<main class="canvas">
  <section class="card card--back" aria-label="Card back">
    <div class="back-pattern" role="img" aria-label="Tonal repeating pattern of the company monogram"></div>
    <div class="back-mark"><span class="mark-square"></span>Renwick Tolliver</div>
  </section>

  <section class="card card--front" aria-label="Card front">
    <div class="company">
      <p class="company__name">Renwick Tolliver</p>
      <p class="company__trade">Construction</p>
    </div>

    <div class="front-mark"><span class="mark-square"></span><span>Renwick<br>Tolliver</span></div>

    <div class="person">
      <p class="person__name">Lionel Ashby</p>
      <p class="person__role">Managing Director</p>
    </div>

    <ul class="contacts">
      <li>
        <svg viewBox="0 0 16 16" aria-hidden="true"><path fill="var(--gold)" d="M3 1h3l1.5 4-2 1.3a9 9 0 0 0 4.2 4.2L11 8.5l4 1.5v3a2 2 0 0 1-2 2A12 12 0 0 1 1 3a2 2 0 0 1 2-2z"/></svg>
        07822254961
      </li>
      <li>
        <svg viewBox="0 0 16 16" aria-hidden="true"><rect x="1" y="3" width="14" height="10" rx="1.5" fill="var(--gold)"/><path d="M1.5 4 8 9l6.5-5" stroke="var(--card-grey)" stroke-width="1.4" fill="none"/></svg>
        info@renwick-tolliver
      </li>
      <li>
        <svg viewBox="0 0 16 16" aria-hidden="true"><circle cx="8" cy="8" r="6.5" fill="none" stroke="var(--gold)" stroke-width="1.6"/><path d="M1.5 8h13M8 1.5c-3 3.5-3 9.5 0 13M8 1.5c3 3.5 3 9.5 0 13" stroke="var(--gold)" stroke-width="1.2" fill="none"/></svg>
        www.renwick-tolliver.co.uk
      </li>
    </ul>
  </section>
</main>
</body>
</html>
```